Upstart Retirement Planning Firm needs help with business card design

Harborview Nest Advisors, LLC is looking for help with business card design. We give advice on investments, insurance, and other financial matters related to retirement. There are some required disclosures that we will provide but mostly we are looking for a professional, classy business card that reflects the theme we have chosen. We have a logo that is attached but we would like to add a phrase; "Turning Your Earned Income Into Retirement Income"

Doubled sided only so that we can add the required disclosures (needed for our industry) on the back of the card. We will provide the exact words for this in 1-2 days.

Target Market(s)

Retirees and Pre-retirees. Professionals 50+ years old

Industry/Entity Type

Financial Planning

Contact Information for Business Card

We currently have two people who will need separate cards so we'd like to have a template so that we can add names for new cards in the future.

For the first run, please show the following information.

Gregor Pelham, MBA, ChFC®, CLU®
Financial Advisor, Registered Representative
gpelham@harborviewnest.example
Phone: (555) 318-2946
Toll Free Fax: (800) 555-0193

Address is
2187 Meadowlark Ridge Rd.
Suite K418
Virginia Beach, VA 23999

Colors
3277b5

Requirements
Must have
• Logo, contact info, small phase to describe business (in description), required legal disclosures on back of the card as follows (in small font)
• Gregor Pelham is a registered representative of and offers securities through Brightmoor Capital Brokerage Corporation, Member FNQX. Brightmoor Capital Brokerage Corporation is a member of the Brightmoor Capital Alliance which is the marketing name for Brightmoor Holding Corporation and its affiliates.
Nice to have
• Rounded edges, raised letters
Should not have
• any colors that aren't in the logo (other than black for font)

```html
<!DOCTYPE html>
<html lang="en">
<head>
<meta charset="utf-8">
<title>Harborview Nest Advisors, LLC — Business Card</title>
<link rel="stylesheet" href="https://fonts.googleapis.com/css2?family=Tinos:wght@400;700&display=swap">
<style>
  :root {
    --brand-blue: #3277b5;
    --brand-blue-deep: #2a67a3;
    --logo-grey: #a9a9a9;
    --ink: #1c1c1c;
    --paper: #ffffff;
    --paper-shade: #f1f1f1;
    --backdrop: #e4e4e2;
  }
  * { box-sizing: border-box; margin: 0; padding: 0; }
  html, body { width: 1200px; height: 892px; overflow: hidden; }
  body {
    background: var(--backdrop);
    font-family: "Tinos", "Times New Roman", serif;
    color: var(--ink);
    position: relative;
  }
  .card {
    position: absolute;
    left: 268px;
    width: 664px;
    height: 380px;
    border-radius: 14px;
    overflow: hidden;
    background: var(--paper);
    box-shadow: 0 6px 18px rgba(0,0,0,0.18);
  }
  .card--front { top: 46px; }
  .card--back  { top: 466px; background: linear-gradient(135deg, var(--paper) 0%, var(--paper-shade) 100%); }

  .card__shape { position: absolute; inset: 0; width: 100%; height: 100%; }

  .wordmark {
    position: absolute;
    text-align: center;
    color: var(--brand-blue);
    font-weight: 400;
    line-height: 1.1;
  }
  .wordmark__rule {
    display: block;
    height: 1px;
    background: var(--logo-grey);
    margin: 10px auto 0;
  }
  .card--front .wordmark { left: 200px; right: 40px; top: 62px; font-size: 27px; letter-spacing: 0.5px; }
  .card--front .wordmark__rule { width: 290px; }

  .holder {
    position: absolute;
    left: 150px;
    top: 168px;
    width: 200px;
    text-align: right;
    font-size: 16px;
    line-height: 1.32;
  }
  .holder__name { color: var(--brand-blue); font-size: 20px; margin-bottom: 2px; }

  .divider {
    position: absolute;
    left: 368px;
    top: 160px;
    width: 1px;
    height: 116px;
    background: var(--logo-grey);
  }

  .contact {
    position: absolute;
    left: 384px;
    top: 162px;
    font-size: 15.5px;
    line-height: 1.42;
    list-style: none;
  }
  .contact__item { display: flex; align-items: center; gap: 8px; white-space: nowrap; }
  .contact__item--plain { padding-left: 22px; }
  .contact__icon { width: 14px; height: 14px; flex: none; }

  .card--back .wordmark { left: 40px; right: 40px; top: 150px; font-size: 40px; letter-spacing: 0.5px; }
  .card--back .wordmark__rule { width: 420px; margin-top: 14px; }
</style>
</head>
<body>

<section class="card card--front" aria-label="Business card front">
  <svg class="card__shape" viewBox="0 0 664 380" preserveAspectRatio="none" aria-hidden="true">
    <defs>
      <linearGradient id="band" x1="0" y1="0" x2="1" y2="1">
        <stop offset="0" stop-color="#3a80bf"/>
        <stop offset="1" stop-color="#2a67a3"/>
      </linearGradient>
    </defs>
    <rect width="664" height="380" fill="url(#band)"/>
    <ellipse cx="420" cy="150" rx="420" ry="300" fill="#ffffff"/>
  </svg>

  <div class="wordmark">Harborview Nest Advisors, LLC<span class="wordmark__rule"></span></div>

  <div class="holder">
    <p class="holder__name">Gregor Pelham, MBA</p>
    <p>ChFC®, CLU®</p>
    <p>Financial Advisor</p>
    <p>Registered Representative</p>
  </div>

  <div class="divider"></div>

  <ul class="contact">
    <li class="contact__item">
      <svg class="contact__icon" viewBox="0 0 14 14" aria-hidden="true"><rect width="14" height="14" rx="2" fill="#3277b5"/><path d="M4 3.5c.6 2.9 2.8 5.6 6.5 7l.8-1.6-1.8-1-.8.8C7.4 8 6 6.7 5.5 5.5l.8-.8-1-1.8z" fill="#fff"/></svg>
      <span>(555) 318-2946</span>
    </li>
    <li class="contact__item">
      <svg class="contact__icon" viewBox="0 0 14 14" aria-hidden="true"><rect width="14" height="14" rx="2" fill="#3277b5"/><path d="M4 3.5c.6 2.9 2.8 5.6 6.5 7l.8-1.6-1.8-1-.8.8C7.4 8 6 6.7 5.5 5.5l.8-.8-1-1.8z" fill="#fff"/></svg>
      <span>(800) 555-0193</span>
    </li>
    <li class="contact__item">
      <svg class="contact__icon" viewBox="0 0 14 14" aria-hidden="true"><rect width="14" height="14" rx="2" fill="#3277b5"/><rect x="3" y="4.2" width="8" height="5.6" fill="#fff"/><path d="M3 4.2l4 3 4-3" fill="none" stroke="#3277b5" stroke-width="0.9"/></svg>
      <span>gpelham@harborviewnest.example</span>
    </li>
    <li class="contact__item">
      <svg class="contact__icon" viewBox="0 0 14 14" aria-hidden="true"><rect width="14" height="14" rx="2" fill="#3277b5"/><path d="M7 2.8a3 3 0 0 0-3 3c0 2.2 3 5.4 3 5.4s3-3.2 3-5.4a3 3 0 0 0-3-3z" fill="#fff"/><circle cx="7" cy="5.8" r="1.1" fill="#3277b5"/></svg>
      <span>2187 Meadowlark Ridge Rd. Suite</span>
    </li>
    <li class="contact__item contact__item--plain"><span>K418 Virginia Beach, VA 23999</span></li>
  </ul>
</section>

<section class="card card--back" aria-label="Business card back">
  <div class="wordmark">Harborview Nest Advisors, LLC<span class="wordmark__rule"></span></div>
</section>

</body>
</html>
```